Kovát Lillas Physiotherapy Business Card Vienna

We need a business card design for a newly created Physiotherapy company based in Vienna Austria.
We seek a simple, modern, minimalist design without too much color variation. The font should look young/fresh, but definitely not childish or so. Since we are a starting Business, we currently haven't got a logo, if you feel like a logo would fit your design, feel free to use one, but it's not necessary.
Target Market(s)
Healthcare, young and elderly people with mobility issues
Industry/Entity Type
Health And Wellness
Contact Information for Business Card
Name: Lilla Kovát
Title description: Physiotherapist
Phone num: +43 664 2951 4086
e-mail: lilla.praxis@bluemail.example
Colors
Designer to choose colors to be used in the design.
Requirements
Must have
- Final design language must be in German, basically, the Title Description needs to be "Physiotherapeutin" the other details remain as in the English Language.
Nice to have
- Simple, modern, minimalist design
Should not have
- too many colors, Obvious use of a skeleton, skull, spline

```html
<!DOCTYPE html>
<html lang="de">
<head>
<meta charset="utf-8">
<title>Kovát Lillas Physiotherapy – Visitenkarte</title>
<link href="https://fonts.googleapis.com/css2?family=Montserrat:wght@700&family=Questrial&display=swap" rel="stylesheet">
<style>
  :root {
    --backdrop: #2c2c2c;
    --card: #151515;
    --card-edge: #1f1f1f;
    --ink: #ffffff;
    --ink-soft: #e6e6e6;
  }
  * { margin: 0; padding: 0; box-sizing: border-box; }
  html, body {
    width: 1200px; height: 900px; overflow: hidden;
    background: var(--backdrop);
  }
  .canvas {
    width: 1200px; height: 900px;
    display: flex; flex-direction: column;
    align-items: center; justify-content: center;
    gap: 44px;
  }
  .card {
    width: 630px; height: 360px;
    background: linear-gradient(135deg, var(--card) 0%, var(--card-edge) 100%);
    box-shadow: 0 18px 40px rgba(0,0,0,0.45);
    position: relative;
    color: var(--ink);
  }
  .wordmark { color: var(--ink); line-height: 1; }
  .wordmark__name {
    display: block;
    font-family: "Montserrat", sans-serif;
    font-weight: 700;
    font-size: 34px;
    letter-spacing: 2px;
  }
  .wordmark__field {
    display: block;
    font-family: "Questrial", sans-serif;
    font-weight: 400;
    font-size: 17px;
    letter-spacing: 10.5px;
    margin-top: 2px;
  }
  .card--front {
    display: flex; align-items: center; justify-content: center;
  }

  .card--back {
    display: flex; align-items: center;
    padding-left: 52px;
  }
  .card--back .wordmark__name { font-size: 27px; letter-spacing: 1.5px; }
  .card--back .wordmark__field { font-size: 14px; letter-spacing: 8.2px; }
  .divider {
    width: 1.5px; height: 112px;
    background: var(--ink);
    margin: 0 32px 0 26px;
  }
  .contact { font-family: "Questrial", sans-serif; color: var(--ink-soft); }
  .contact__name {
    font-family: "Montserrat", sans-serif; font-weight: 700;
    font-size: 23px; letter-spacing: 1.5px; color: var(--ink);
  }
  .contact__title { font-size: 15px; margin-bottom: 16px; }
  .contact__line {
    display: flex; align-items: center; gap: 9px;
    font-size: 16px; margin-top: 6px;
  }
  .contact__icon { width: 12px; height: 12px; flex: none; }
</style>
</head>
<body>
<main class="canvas">
  <section class="card card--front" aria-label="Vorderseite">
    <div class="wordmark">
      <span class="wordmark__name">KOVÁT LILLAS</span>
      <span class="wordmark__field">PHYSIOTHERAPY</span>
    </div>
  </section>

  <section class="card card--back" aria-label="Rückseite">
    <div class="wordmark">
      <span class="wordmark__name">KOVÁT LILLAS</span>
      <span class="wordmark__field">PHYSIOTHERAPY</span>
    </div>
    <div class="divider"></div>
    <div class="contact">
      <div class="contact__name">Lilla Kovát</div>
      <div class="contact__title">Physiotherapeutin</div>
      <div class="contact__line">
        <svg class="contact__icon" viewBox="0 0 12 12" aria-hidden="true">
          <path d="M3 1 L4.6 3.2 L3.6 4.4 Q4.8 7 7.6 8.4 L8.8 7.4 L11 9 L10 11 Q4 10.6 1 2 Z" fill="none" stroke="#e6e6e6" stroke-width="1"/>
        </svg>
        <span>+43 664 2951 4086</span>
      </div>
      <div class="contact__line">
        <svg class="contact__icon" viewBox="0 0 12 12" aria-hidden="true">
          <rect x="0.8" y="2.5" width="10.4" height="7" fill="none" stroke="#e6e6e6" stroke-width="1"/>
          <path d="M0.8 2.5 L6 6.6 L11.2 2.5" fill="none" stroke="#e6e6e6" stroke-width="1"/>
        </svg>
        <span>lilla.praxis@bluemail.example</span>
      </div>
    </div>
  </section>
</main>
</body>
</html>
```